Commercial / Truck Battery Label

We need a high definition label design to send to a commercial printer for a Commercial/Truck Battery Label
I will upload our current truck battery label for you to get an idea of what we are looking for. Along with some competitor images and other logos for the label that we have on file. If we need to purchase a few images to make the label we can do that but need to see the design first.
The Labels need to have a plain white area which is 60mm Long x 40mm High along the bottom left corner. We will use this area for the battery specifications.
The Top Six Warning Icons downloaded also need to be on the label, perhaps along the bottom to the right of the white area in pairs. The icons size can be between 10mm x 10mm and 20mm x 20mm
The dimensions of the label need to be 390mm Long and the height needs to be both 140mm and 180mm. Same label 2 different sizes.
I would like to keep the terms : "SUPER HEAVY DUTY" and "THE IRON CHARGE THAT HOLDS" on the label somewhere. Maybe replacing the word batteries or commercial with SUPER HEAVY DUTY under the right side of the VOLTCRANE Logo.
The labels will be used predominantly on Black batteries, so a colour scheme or design to suit that.
I don't mind a completely fresh design or a reworking of the old design.

```html
<!DOCTYPE html>
<html lang="en">
<head>
<meta charset="utf-8">
<title>VOLTCRANE Super Heavy Duty Battery Labels</title>
<link rel="stylesheet" href="https://fonts.googleapis.com/css2?family=Anton&family=Saira+Condensed:ital,wght@0,700;0,800;1,800;1,900&family=Open+Sans:wght@400;700&display=swap">
<style>
  :root {
    --page: #ececec;
    --carbon-dark: #151515;
    --carbon-light: #2a2a2a;
    --brand-blue: #0f2f86;
    --brand-red: #e10a1d;
    --white: #ffffff;
    --ink: #111111;
    --rule-grey: #9a9a9a;
    --icon-black: #0c0c0c;
  }
  html, body {
    margin: 0;
    padding: 0;
    width: 1200px;
    height: 1158px;
    overflow: hidden;
    background: var(--page);
  }
  .canvas {
    position: relative;
    width: 1200px;
    height: 1158px;
  }
  .label {
    position: absolute;
    display: block;
  }
  .label--tall { left: 154px; top: 150px; }
  .label--short { left: 146px; top: 682px; }
  .brand-mark { font-family: "Anton", sans-serif; fill: var(--brand-blue); }
  .product-name { font-family: "Anton", sans-serif; fill: var(--white); }
  .range-word {
    font-family: "Saira Condensed", sans-serif; font-weight: 900; font-style: italic;
    fill: var(--brand-blue); stroke: var(--white); stroke-width: 2; paint-order: stroke;
  }
  .duty-line { font-family: "Saira Condensed", sans-serif; font-weight: 800; font-style: italic; fill: var(--white); }
  .tagline { font-family: "Saira Condensed", sans-serif; font-weight: 800; font-style: italic; fill: var(--white); }
  .icon-caption { font-family: "Saira Condensed", sans-serif; font-weight: 700; fill: var(--white); }
  .spec-title { font-family: "Open Sans", sans-serif; font-weight: 700; fill: var(--ink); }
  .spec-body { font-family: "Open Sans", sans-serif; font-weight: 400; fill: var(--ink); }
  .sprite { position: absolute; width: 0; height: 0; }
</style>
</head>
<body>
<div class="canvas">

<svg class="sprite" aria-hidden="true">
  <defs>
    <linearGradient id="carbon" x1="0" y1="0" x2="1" y2="1">
      <stop offset="0" stop-color="#2b2b2b"/>
      <stop offset="1" stop-color="#141414"/>
    </linearGradient>
    <linearGradient id="field-scene" x1="0" y1="0" x2="0" y2="1">
      <stop offset="0" stop-color="#8fb6de"/>
      <stop offset="0.55" stop-color="#c9d9e6"/>
      <stop offset="0.7" stop-color="#3f8a2f"/>
      <stop offset="1" stop-color="#2d6a22"/>
    </linearGradient>
    <linearGradient id="road-scene" x1="0" y1="0" x2="1" y2="1">
      <stop offset="0" stop-color="#5e6f7e"/>
      <stop offset="0.5" stop-color="#8b7a5c"/>
      <stop offset="0.75" stop-color="#e59a2f"/>
      <stop offset="1" stop-color="#4a4a4a"/>
    </linearGradient>
    <symbol id="icon-manual" viewBox="0 0 50 50">
      <rect x="15" y="12" width="18" height="24" fill="none" stroke="#fff" stroke-width="2.4"/>
      <path d="M19 18h10M19 23h10M19 28h7" stroke="#fff" stroke-width="2"/>
      <path d="M29 36l8-10 3 2-8 10z" fill="#fff"/>
    </symbol>
    <symbol id="icon-goggles" viewBox="0 0 50 50">
      <rect x="11" y="19" width="28" height="11" rx="5" fill="none" stroke="#fff" stroke-width="2.4"/>
      <circle cx="19" cy="24.5" r="3" fill="#fff"/>
      <circle cx="31" cy="24.5" r="3" fill="#fff"/>
      <path d="M8 24h3M39 24h3" stroke="#fff" stroke-width="2.4"/>
    </symbol>
    <symbol id="icon-children" viewBox="0 0 50 50">
      <circle cx="25" cy="25" r="15" fill="none" stroke="var(--brand-red)" stroke-width="3.5"/>
      <circle cx="25" cy="18" r="3" fill="#fff"/>
      <path d="M25 21v8M20 25h10M25 29l-4 6M25 29l4 6" stroke="#fff" stroke-width="2.4"/>
      <path d="M14 14l22 22" stroke="var(--brand-red)" stroke-width="3.5"/>
    </symbol>
    <symbol id="icon-corrosive" viewBox="0 0 50 50">
      <path d="M13 29h14l6 5H17z" fill="#fff"/>
      <path d="M28 12l8 4-2 4-8-4z" fill="#fff"/>
      <circle cx="30" cy="23" r="1.6" fill="#fff"/>
      <circle cx="27" cy="26" r="1.4" fill="#fff"/>
    </symbol>
    <symbol id="icon-no-flame" viewBox="0 0 50 50">
      <circle cx="25" cy="25" r="15" fill="none" stroke="var(--brand-red)" stroke-width="3.5"/>
      <path d="M25 14c4 6 8 9 6 15a6 6 0 0 1-12 0c0-4 3-5 3-9 2 2 3 3 3 5 1-3 1-7 0-11z" fill="#fff"/>
      <path d="M14 14l22 22" stroke="var(--brand-red)" stroke-width="3.5"/>
    </symbol>
    <symbol id="icon-explosive" viewBox="0 0 50 50">
      <path d="M25 11l3 8 6-4-2 8 7 2-7 3 3 7-7-3-3 8-3-8-7 3 3-7-7-3 7-2-2-8 6 4z" fill="#fff"/>
      <rect x="13" y="34" width="24" height="3" fill="#fff"/>
    </symbol>
  </defs>
</svg>

<!-- 180 mm label -->
<svg class="label label--tall" width="904" height="416" viewBox="0 0 904 416">
  <rect width="904" height="416" fill="url(#carbon)"/>
  <polygon points="668,0 904,0 904,416 434,416 530,258 612,258" fill="var(--brand-red)"/>
  <g role="img" aria-label="Green farm tractor in a crop field under a blue sky">
    <polygon points="676,0 904,0 904,112 652,112" fill="url(#field-scene)"/>
  </g>
  <g role="img" aria-label="Orange semi truck driving along a highway">
    <polygon points="650,117 904,117 904,256 618,256" fill="url(#road-scene)"/>
  </g>
  <polygon points="0,342 478,342 476,346 0,346" fill="var(--rule-grey)"/>
  <polygon points="0,346 476,346 434,416 0,416" fill="var(--white)"/>

  <text class="brand-mark" x="186" y="82" font-size="58" textLength="240" lengthAdjust="spacingAndGlyphs">HALVEK</text>
  <text class="product-name" x="22" y="226" font-size="150" textLength="604" lengthAdjust="spacingAndGlyphs">VOLTCRANE</text>
  <rect x="22" y="238" width="344" height="10" fill="var(--brand-red)" stroke="var(--white)" stroke-width="2"/>
  <text class="range-word" x="366" y="267" font-size="44" textLength="288" lengthAdjust="spacingAndGlyphs">BATTERIES</text>
  <text class="duty-line" x="30" y="330" font-size="56" textLength="440" lengthAdjust="spacingAndGlyphs">SUPER HEAVY DUTY</text>

  <g class="warning-icons">
    <circle cx="578" cy="310" r="25" fill="var(--icon-black)" stroke="var(--white)" stroke-width="2"/>
    <use href="#icon-manual" x="553" y="285" width="50" height="50"/>
    <circle cx="636" cy="310" r="25" fill="var(--icon-black)" stroke="var(--white)" stroke-width="2"/>
    <use href="#icon-goggles" x="611" y="285" width="50" height="50"/>
    <circle cx="692" cy="310" r="25" fill="var(--icon-black)" stroke="var(--white)" stroke-width="2"/>
    <use href="#icon-children" x="667" y="285" width="50" height="50"/>
    <circle cx="747" cy="310" r="25" fill="var(--icon-black)" stroke="var(--white)" stroke-width="2"/>
    <use href="#icon-corrosive" x="722" y="285" width="50" height="50"/>
    <circle cx="802" cy="310" r="25" fill="var(--icon-black)" stroke="var(--white)" stroke-width="2"/>
    <use href="#icon-no-flame" x="777" y="285" width="50" height="50"/>
    <circle cx="858" cy="310" r="25" fill="var(--icon-black)" stroke="var(--white)" stroke-width="2"/>
    <use href="#icon-explosive" x="833" y="285" width="50" height="50"/>
  </g>
  <g class="icon-caption" font-size="6.5" text-anchor="middle">
    <text x="578" y="343">READ OPERATING</text><text x="578" y="351">INSTRUCTIONS</text>
    <text x="636" y="343">SHIELD EYES</text><text x="636" y="351">EYE PROTECTION</text>
    <text x="692" y="343">KEEP AWAY</text><text x="692" y="351">FROM CHILDREN</text>
    <text x="747" y="343">NO SMOKING</text><text x="747" y="351">NO SPARKS</text>
    <text x="802" y="343">BATTERY ACID</text><text x="802" y="351">CORROSIVE &amp; POISONOUS</text>
    <text x="858" y="343">EXPLOSIVE</text><text x="858" y="351">GASES</text>
  </g>
  <rect x="470" y="363" width="416" height="2" fill="var(--white)"/>
  <text class="tagline" x="470" y="402" font-size="38" textLength="415" lengthAdjust="spacingAndGlyphs">THE IRON CHARGE THAT HOLDS</text>

  <text class="spec-title" x="22" y="366" font-size="11">Specification:</text>
  <g class="spec-body" font-size="8.6">
    <text x="22" y="380" textLength="410" lengthAdjust="spacingAndGlyphs">Lorem ipsum dolor sit amet, consectetuer adipiscing elit, sed diam nonummy nibh euismod tincidunt</text>
    <text x="22" y="392" textLength="400" lengthAdjust="spacingAndGlyphs">ut laoreet dolore magna aliquam erat volutpat. Ut wisi enim ad minim veniam, quis nostrud exerci</text>
    <text x="22" y="404" textLength="375" lengthAdjust="spacingAndGlyphs">tation ullamcorper suscipit lobortis nisl ut aliquip ex ea commodo consequat. Duis autem vel</text>
  </g>
</svg>

<!-- 140 mm label -->
<svg class="label label--short" width="904" height="324" viewBox="0 0 904 324">
  <rect width="904" height="324" fill="url(#carbon)"/>
  <polygon points="708,0 904,0 904,324 534,324 586,198 664,198" fill="var(--brand-red)"/>
  <g role="img" aria-label="Green farm tractor in a crop field under a blue sky">
    <polygon points="716,0 904,0 904,84 700,84" fill="url(#field-scene)"/>
  </g>
  <g role="img" aria-label="Orange semi truck driving along a highway">
    <polygon points="698,88 904,88 904,196 676,196" fill="url(#road-scene)"/>
  </g>
  <polygon points="0,269 572,269 570,272 0,272" fill="var(--rule-grey)"/>
  <polygon points="0,272 570,272 548,324 0,324" fill="var(--white)"/>

  <text class="brand-mark" x="500" y="52" font-size="44" textLength="170" lengthAdjust="spacingAndGlyphs">HALVEK</text>
  <text class="product-name" x="38" y="178" font-size="132" textLength="560" lengthAdjust="spacingAndGlyphs">VOLTCRANE</text>
  <rect x="38" y="190" width="316" height="8" fill="var(--brand-red)" stroke="var(--white)" stroke-width="2"/>
  <text class="range-word" x="356" y="220" font-size="38" textLength="266" lengthAdjust="spacingAndGlyphs">BATTERIES</text>
  <text class="duty-line" x="38" y="263" font-size="42" textLength="328" lengthAdjust="spacingAndGlyphs">SUPER HEAVY DUTY</text>

  <g class="warning-icons">
    <circle cx="653" cy="236" r="20" fill="var(--icon-black)" stroke="var(--white)" stroke-width="2"/>
    <use href="#icon-manual" x="633" y="216" width="40" height="40"/>
    <circle cx="698" cy="236" r="20" fill="var(--icon-black)" stroke="var(--white)" stroke-width="2"/>
    <use href="#icon-goggles" x="678" y="216" width="40" height="40"/>
    <circle cx="741" cy="236" r="20" fill="var(--icon-black)" stroke="var(--white)" stroke-width="2"/>
    <use href="#icon-children" x="721" y="216" width="40" height="40"/>
    <circle cx="783" cy="236" r="20" fill="var(--icon-black)" stroke="var(--white)" stroke-width="2"/>
    <use href="#icon-corrosive" x="763" y="216" width="40" height="40"/>
    <circle cx="826" cy="236" r="20" fill="var(--icon-black)" stroke="var(--white)" stroke-width="2"/>
    <use href="#icon-no-flame" x="806" y="216" width="40" height="40"/>
    <circle cx="868" cy="236" r="20" fill="var(--icon-black)" stroke="var(--white)" stroke-width="2"/>
    <use href="#icon-explosive" x="848" y="216" width="40" height="40"/>
  </g>
  <g class="icon-caption" font-size="5" text-anchor="middle">
    <text x="653" y="263">READ OPERATING</text><text x="653" y="269">INSTRUCTIONS</text>
    <text x="698" y="263">SHIELD EYES</text><text x="698" y="269">EYE PROTECTION</text>
    <text x="741" y="263">KEEP AWAY</text><text x="741" y="269">FROM CHILDREN</text>
    <text x="783" y="263">NO SMOKING</text><text x="783" y="269">NO SPARKS</text>
    <text x="826" y="263">BATTERY ACID</text><text x="826" y="269">CORROSIVE &amp; POISONOUS</text>
    <text x="868" y="263">EXPLOSIVE</text><text x="868" y="269">GASES</text>
  </g>
  <rect x="566" y="277" width="324" height="2" fill="var(--white)"/>
  <text class="tagline" x="566" y="308" font-size="30" textLength="322" lengthAdjust="spacingAndGlyphs">THE IRON CHARGE THAT HOLDS</text>

  <text class="spec-title" x="16" y="287" font-size="9">Specification:</text>
  <g class="spec-body" font-size="7.2">
    <text x="16" y="298" textLength="520" lengthAdjust="spacingAndGlyphs">Lorem ipsum dolor sit amet, consectetuer adipiscing elit, sed diam nonummy nibh euismod tincidunt ut laoreet dolore magna aliquam erat volutpat. Ut wisi enim ad</text>
    <text x="16" y="308" textLength="420" lengthAdjust="spacingAndGlyphs">minim veniam, quis nostrud exerci tation ullamcorper suscipit lobortis nisl ut aliquip ex ea commodo consequat. Duis autem vel</text>
  </g>
</svg>

</div>
</body>
</html>
```